Velora Entertainment

Logo for business card design

Target Market(s)

potential film investors and screenwriters

Industry/Entity Type

Business

Contact Information for Business Card

as shown, website here is a placeholder position

Requirements
Must have
• great visual appeal
Nice to have
• harmony of colors; must evoke spirit of
• U.S.-China cooperation

```html
<!DOCTYPE html>
<html lang="en">
<head>
<meta charset="utf-8">
<title>Velora Entertainment — Business Card</title>
<link rel="stylesheet" href="https://fonts.googleapis.com/css2?family=Open+Sans:ital,wght@0,400;0,600;0,700;1,700&display=swap">
<style>
  :root {
    --page-bg: #8f9090;
    --card-front: #f1f1f3;
    --card-back: #848587;
    --ink: #1d1d1d;
    --accent-red: #c8101d;
    --accent-yellow: #e3b800;
    --accent-blue: #1c1f86;
    --band-gray: #a2a3a5;
    --logo-light: #eef2f5;
  }
  * { box-sizing: border-box; margin: 0; padding: 0; }
  html, body {
    width: 1105px; height: 1200px; overflow: hidden;
    background: var(--page-bg);
    font-family: "Open Sans", Arial, sans-serif;
    color: var(--ink);
  }
  .card {
    position: absolute;
    left: 180px;
    width: 746px;
    height: 427px;
    overflow: hidden;
  }
  .card-front { top: 110px; background: var(--card-front); }
  .card-back { top: 660px; background: var(--card-back); }

  .holder-name {
    position: absolute; left: 48px; top: 42px;
    font-size: 24px; font-weight: 600; color: var(--accent-red);
  }
  .holder-title {
    position: absolute; left: 48px; top: 76px;
    font-size: 19px;
  }
  .address {
    position: absolute; left: 48px; top: 158px;
    font-size: 19px; line-height: 29px;
  }
  .contact-list {
    position: absolute; left: 48px; top: 228px;
    list-style: none; font-size: 19px; line-height: 32px;
  }
  .contact-label { color: var(--accent-red); font-weight: 700; }

  .brand {
    position: absolute;
    display: flex; align-items: center; gap: 12px;
    font-weight: 700; font-size: 27px; letter-spacing: 0.5px;
    white-space: nowrap;
  }
  .brand-mark { width: 22px; height: 22px; flex: none; }
  .card-front .brand { right: 48px; top: 246px; color: var(--accent-blue); }
  .card-front .brand-mark { background: var(--accent-red); }
  .card-back .brand {
    left: 50%; top: 50%; transform: translate(-50%, -50%);
    color: var(--logo-light); font-size: 32px;
  }
  .card-back .brand-mark { background: var(--logo-light); }

  .footer-graphic { position: absolute; left: 0; bottom: 0; width: 746px; height: 46px; }
  .website {
    position: absolute; right: 48px; bottom: 9px;
    font-size: 19px; font-weight: 700; font-style: italic; letter-spacing: 1.5px;
  }
</style>
</head>
<body>
  <section class="card card-front" aria-label="Business card front">
    <h1 class="holder-name">Marcus Hale</h1>
    <p class="holder-title">CEO/Founder</p>
    <p class="address">2140 Harbor View Road<br>Juneau,Alaska 99801</p>
    <ul class="contact-list">
      <li><span class="contact-label">P :</span> 907 512 4380</li>
      <li><span class="contact-label">F :</span> 907 512 4391</li>
      <li><span class="contact-label">M :</span> 907 688 2716</li>
      <li>marcus@veloraent.com</li>
    </ul>
    <div class="brand"><span class="brand-mark"></span>Velora Entertainment</div>
    <svg class="footer-graphic" viewBox="0 0 746 46" aria-hidden="true">
      <polygon points="0,8 140,8 130,27 0,27" fill="var(--accent-red)"/>
      <polygon points="133,8 278,8 268,27 123,27" fill="var(--accent-yellow)"/>
      <polygon points="271,8 417,8 407,27 261,27" fill="var(--accent-blue)"/>
      <polygon points="430,0 746,0 746,46 395,46" fill="var(--band-gray)"/>
    </svg>
    <p class="website">www.veloraent.com</p>
  </section>

  <section class="card card-back" aria-label="Business card back">
    <div class="brand"><span class="brand-mark"></span>Velora Entertainment</div>
  </section>
</body>
</html>
```